Redesign Website - Current one too plain

The description is in the uploaded file. Please let me know if you need any more information. I'd prefer it if someone could implement the design to a WordPress site but the best design will win, regardless.
I would like the forms to look nice as well
UPDATE:
I don't think we can use the images that I provided, I think they make the site look a bit 'cheap' and I really don't know how to replace them. One thought I have had is to make the "Simple, Unique, Effective" a second feature on the right side of the page with the search on the left
Target Market(s)
Small companies, private sellers of cars and people who rent their caravan/holiday home out
Industry/Entity Type
Advertising
Number of Pages Required
3 page
Colors
Designer to choose colors to be used in the design.
Look and feel
Each slider illustrates characteristics of the customer's brand and the style your logo design should communicate.

```html
<!DOCTYPE html>
<html lang="en">
<head>
<meta charset="utf-8">
<title>PLATEO.com – Advertise your code</title>
<link href="https://fonts.googleapis.com/css2?family=Baloo+2:wght@600;700;800&family=Lato:wght@400;700&display=swap" rel="stylesheet">
<style>
:root{
  --lime:#e6ff00;
  --dark:#2f2f2f;
  --ink:#111;
  --text:#3a3a3a;
  --muted:#8a8a8a;
  --soft:#f4f4f4;
  --line:#e4e4e4;
  --white:#fff;
}
*{box-sizing:border-box;margin:0;padding:0}
html,body{width:1200px;height:3598px;overflow:hidden;background:var(--white)}
body{position:relative;font-family:"Lato",sans-serif;color:var(--text)}
h1,h2,h3,h4{font-family:"Baloo 2",sans-serif;color:var(--ink);font-weight:800;line-height:1}

/* header */
.brand{position:absolute;background:var(--dark);display:flex;align-items:center;justify-content:center;gap:8px;font-family:"Lato",sans-serif;font-weight:700;color:var(--lime);letter-spacing:3px}
.brand .dot{width:12px;height:12px;background:var(--lime);border-radius:50%}
.site-header .brand{left:112px;top:21px;width:208px;height:66px;font-size:21px}
.nav{position:absolute;top:46px;left:507px;display:flex;gap:33px;font-size:15px;color:#222}
.login{position:absolute;left:965px;top:31px;width:123px;height:44px;background:var(--dark);color:#fff;border-radius:6px 14px 14px 14px;font-family:"Baloo 2",sans-serif;font-weight:700;font-size:13px;letter-spacing:.5px;display:flex;align-items:center;justify-content:center;gap:8px}

/* hero */
.hero{position:absolute;left:32px;top:110px;width:1139px;height:600px;border-radius:44px;overflow:hidden;background:#363636}
.hero-photo{position:absolute;inset:0;background:radial-gradient(ellipse at 50% 55%,#5a5a5a 0%,#454545 35%,#363636 70%)}
.plate{position:absolute;left:0;right:0;top:150px;text-align:center;font-family:"Baloo 2",sans-serif;font-weight:800;font-size:112px;color:#fff;line-height:1}
.chev{position:absolute;width:18px;height:18px;border-left:3px solid #fff;border-top:3px solid #fff}
.chev.up{transform:rotate(45deg)}
.chev.down{transform:rotate(225deg)}
.cat{position:absolute;top:341px;width:128px;height:44px;background:#fff;border-radius:6px 16px 16px 16px;font-family:"Baloo 2",sans-serif;font-weight:700;font-size:12px;color:#222;display:flex;align-items:center;justify-content:center}
.search-btn{position:absolute;left:504px;top:428px;width:128px;height:42px;background:var(--lime);border-radius:6px 16px 16px 16px;font-family:"Baloo 2",sans-serif;font-weight:700;font-size:12px;color:#111;display:flex;align-items:center;justify-content:center}

/* features */
.feature{position:absolute;top:798px;width:305px;height:244px;background:#fff;border-radius:10px;box-shadow:0 6px 24px rgba(0,0,0,.07);overflow:hidden;padding:36px 29px}
.feature .wash{position:absolute;right:-30px;top:-10px;width:200px;height:270px;background:#fbffe6;border-radius:40% 60% 50% 50%}
.feature.dark{background:var(--dark);height:281px}
.feature.dark .wash{background:#3b3b3b}
.feature .icon{position:relative;width:50px;height:50px;border-radius:50%;background:var(--lime);display:flex;align-items:center;justify-content:center}
.feature.dark .icon{background:#1f1f1f}
.feature h3{position:relative;font-size:26px;margin-top:22px}
.feature.dark h3{color:#fff;margin-top:18px}
.feature p{position:relative;font-size:14px;line-height:28px;margin-top:10px;color:#333;width:225px}
.feature.dark p{color:#eee}
.feature .more{position:relative;display:inline-block;margin-top:12px;font-family:"Baloo 2",sans-serif;font-weight:700;font-size:14px;color:var(--lime);text-decoration:underline}

/* about */
.about{position:absolute;left:0;top:1190px;width:1200px;height:676px;background:var(--soft)}
.about-photo{position:absolute;left:123px;top:53px;width:503px;height:584px;border-radius:24px;background:linear-gradient(150deg,#8d9296 0%,#6a6f74 50%,#3e4246 100%)}
.about h2{position:absolute;left:665px;top:70px;font-size:44px}
.about-item{position:absolute;left:665px;width:440px}
.about-item h4{font-size:25px;display:flex;align-items:center;gap:8px}
.about-item h4::before{content:"";width:9px;height:9px;border:3px solid var(--lime);border-radius:50%}
.about-item p{margin-left:22px;font-size:14px;line-height:30px;color:#333;margin-top:6px}

/* testimonials */
.testimonials h2{position:absolute;left:0;right:0;top:1960px;text-align:center;font-size:42px}
.avatar{position:absolute;border-radius:50%;background:linear-gradient(160deg,#c9b8a6,#7d6b5d);border:3px solid #fff;box-shadow:0 2px 8px rgba(0,0,0,.12)}
.client-name{position:absolute;left:0;right:0;top:2192px;text-align:center;font-weight:700;font-size:18px;color:#222}
.quote{position:absolute;left:240px;width:720px;top:2232px;text-align:center;font-size:15px;line-height:28px;color:#333}
.dots{position:absolute;top:2342px;left:560px;display:flex;gap:6px}
.dots span{width:9px;height:9px;border-radius:50%;background:#e2e2e2}
.dots span.on{background:var(--lime)}

/* contact */
.contact{position:absolute;left:0;top:2448px;width:1200px;height:497px;background:var(--soft)}
.contact h2{position:absolute;left:0;right:0;top:60px;text-align:center;font-size:42px}
.info{position:absolute;left:110px;display:flex;gap:14px;width:310px}
.info .ring{flex:none;width:50px;height:50px;border:2px solid #333;border-radius:50%;display:flex;align-items:center;justify-content:center}
.info h4{font-size:20px;margin-top:2px}
.info p{font-size:14px;line-height:24px;color:#333;margin-top:2px}
.field{position:absolute;background:#fff;font-size:14px;color:#999;padding:17px 24px;box-shadow:0 4px 16px rgba(0,0,0,.04)}
.submit{position:absolute;left:433px;top:359px;width:317px;height:53px;background:var(--lime);font-family:"Baloo 2",sans-serif;font-weight:700;font-size:14px;color:#111;display:flex;align-items:center;justify-content:center}

/* newsletter */
.news h2{position:absolute;left:0;right:0;top:3036px;text-align:center;font-size:42px}
.news .email{position:absolute;left:237px;top:3128px;width:540px;height:54px;border-radius:27px;background:#ececec;font-size:16px;color:#444;padding:17px 31px}
.news .subscribe{position:absolute;left:795px;top:3128px;width:179px;height:54px;border-radius:27px;background:var(--lime);font-family:"Baloo 2",sans-serif;font-weight:700;font-size:17px;color:#111;display:flex;align-items:center;justify-content:center}

/* footer */
.rule{position:absolute;left:110px;width:980px;height:1px;background:var(--line)}
.site-footer .brand{left:117px;top:3298px;width:208px;height:66px;font-size:22px}
.fcol{position:absolute;top:3300px}
.fcol h4{font-size:23px;font-weight:700}
.fcol ul{list-style:none;margin-top:10px;font-size:14px;color:#333}
.fcol li{line-height:33px;display:flex;align-items:center;gap:5px}
.social{display:flex;gap:10px;margin-top:16px}
.social span{width:26px;height:26px;border-radius:50%;background:#ddd}
.social span:first-child{background:#222}
.copyright{position:absolute;left:0;right:0;top:3538px;text-align:center;font-size:14px;color:#333}
.copyright a{color:#bcd000;text-decoration:underline}
</style>
</head>
<body>

<header class="site-header">
  <div class="brand"><span class="dot"></span>PLATEO.com</div>
  <nav class="nav"><span>Home</span><span>Advertise</span><span>Contact</span><span>Register</span><span>Search</span></nav>
  <div class="login">
    <svg width="12" height="12" viewBox="0 0 12 12"><circle cx="6" cy="3.5" r="2.8" fill="#fff"/><path d="M1 12c0-3 2.3-4.8 5-4.8s5 1.8 5 4.8z" fill="#fff"/></svg>
    LOGIN
  </div>
</header>

<section class="hero">
  <div class="hero-photo" role="img" aria-label="Cars and a caravan holiday home with personalised number plates, shown in dark grey tones"></div>
  <span class="chev up" style="left:543px;top:134px"></span>
  <span class="chev up" style="left:603px;top:134px"></span>
  <div class="plate">A1</div>
  <span class="chev down" style="left:543px;top:260px"></span>
  <span class="chev down" style="left:603px;top:260px"></span>
  <div class="cat" style="left:359px">CAR</div>
  <div class="cat" style="left:504px">CARAVAN</div>
  <div class="cat" style="left:650px">COMPANY</div>
  <div class="search-btn">SEARCH &gt;</div>
</section>

<section class="features">
  <article class="feature" style="left:110px">
    <div class="wash"></div>
    <div class="icon"><svg width="26" height="26" viewBox="0 0 26 26" fill="none" stroke="#111" stroke-width="2" stroke-linecap="round"><path d="M4 22L16 10"/><path d="M18 3v4M16 5h4M22 9v3M20.5 10.5h3M12 4v2M11 5h2"/></svg></div>
    <h3>Simple</h3>
    <p>create &nbsp;your advert and display your code</p>
  </article>
  <article class="feature dark" style="left:447px">
    <div class="wash"></div>
    <div class="icon"><svg width="26" height="26" viewBox="0 0 26 26" fill="none" stroke="#e6ff00" stroke-width="2"><circle cx="11" cy="11" r="8"/><circle cx="11" cy="11" r="4"/><path d="M14 14l8 8" stroke-linecap="round"/></svg></div>
    <h3>Unique</h3>
    <p>customers find you by an easy-to-re-member code</p>
    <span class="more">Learn More</span>
  </article>
  <article class="feature" style="left:784px">
    <div class="wash"></div>
    <div class="icon"><svg width="30" height="30" viewBox="0 0 30 30" fill="none" stroke="#111" stroke-width="2"><circle cx="15" cy="15" r="11"/><circle cx="15" cy="15" r="7"/><circle cx="15" cy="15" r="3"/><path d="M15 15l9-9" stroke-linecap="round"/></svg></div>
    <h3>Effective</h3>
    <p>customers are directed to you and not a list of your competitors</p>
  </article>
</section>

<section class="about">
  <div class="about-photo" role="img" aria-label="Photo of a business team meeting around a conference table"></div>
  <h2>About</h2>
  <div class="about-item" style="top:162px"><h4>Lorem Ipsum</h4><p>Lorem ipsum dolor sit amet, consectetur adipiscing elit, sed do eiusmod tempor incididunt ut labore et dolore magna aliqua. Quis ipsum suspendisse ultrices gravida.</p></div>
  <div class="about-item" style="top:317px"><h4>Lorem Ipsum</h4><p>Lorem ipsum dolor sit amet, consectetur adipiscing elit, sed do eiusmod tempor incididunt ut labore et dolore magna aliqua. Quis ipsum suspendisse ultrices gravida.</p></div>
  <div class="about-item" style="top:471px"><h4>Lorem Ipsum</h4><p>Lorem ipsum dolor sit amet, consectetur adipiscing elit, sed do eiusmod tempor incididunt ut labore et dolore magna aliqua. Quis ipsum suspendisse ultrices gravida.</p></div>
</section>

<section class="testimonials">
  <h2>What Our Clients Say</h2>
  <div class="avatar" role="img" aria-label="Client portrait" style="left:190px;top:2058px;width:62px;height:62px"></div>
  <div class="avatar" role="img" aria-label="Client portrait" style="left:279px;top:2114px;width:62px;height:62px"></div>
  <div class="avatar" role="img" aria-label="Client portrait" style="left:367px;top:2058px;width:62px;height:62px"></div>
  <div class="avatar" role="img" aria-label="Client portrait" style="left:455px;top:2114px;width:62px;height:62px"></div>
  <div class="avatar" role="img" aria-label="Portrait of featured client Daniel" style="left:548px;top:2043px;width:96px;height:96px"></div>
  <div class="avatar" role="img" aria-label="Client portrait" style="left:676px;top:2114px;width:62px;height:62px"></div>
  <div class="avatar" role="img" aria-label="Client portrait" style="left:764px;top:2058px;width:62px;height:62px"></div>
  <div class="avatar" role="img" aria-label="Client portrait" style="left:852px;top:2114px;width:62px;height:62px"></div>
  <div class="avatar" role="img" aria-label="Client portrait" style="left:941px;top:2058px;width:62px;height:62px"></div>
  <div class="client-name">Daniel</div>
  <p class="quote">Lorem ipsum dolor sit amet, consectetur adipiscing elit, sed do eiusmod tempor incididunt ut labore et dolore magna aliqua. Quis ipsum suspendisse ultrices gravida. Risus commodo viverra maecenas accumsan lacus vel facilisis.</p>
  <div class="dots"><span></span><span></span><span></span><span class="on"></span><span></span><span></span></div>
</section>

<section class="contact">
  <h2>Contact Us</h2>
  <div class="info" style="top:155px">
    <span class="ring"><svg width="14" height="18" viewBox="0 0 14 18"><path d="M7 0a7 7 0 0 0-7 7c0 5 7 11 7 11s7-6 7-11a7 7 0 0 0-7-7z" fill="#333"/><circle cx="7" cy="7" r="2.5" fill="#fff"/></svg></span>
    <div><h4>Location</h4><p>112/b plateo sit amet, consectetur adipiscing</p></div>
  </div>
  <div class="info" style="top:267px">
    <span class="ring"><svg width="16" height="16" viewBox="0 0 24 24"><path fill="#333" d="M6.6 10.8a15 15 0 0 0 6.6 6.6l2.2-2.2a1 1 0 0 1 1-.25 11.4 11.4 0 0 0 3.6.57 1 1 0 0 1 1 1V20a1 1 0 0 1-1 1A17 17 0 0 1 3 4a1 1 0 0 1 1-1h3.5a1 1 0 0 1 1 1c0 1.25.2 2.45.57 3.57a1 1 0 0 1-.25 1z"/></svg></span>
    <div><h4>Phone</h4><p>+1 555 010 0199</p></div>
  </div>
  <div class="info" style="top:356px">
    <span class="ring"><svg width="16" height="12" viewBox="0 0 16 12"><rect width="16" height="12" rx="1.5" fill="#333"/><path d="M1 1.5l7 5 7-5" stroke="#fff" stroke-width="1.4" fill="none"/></svg></span>
    <div><h4>Email</h4><p>info@plateo.com</p></div>
  </div>
  <div class="field" style="left:433px;top:155px;width:317px;height:53px">Name</div>
  <div class="field" style="left:433px;top:223px;width:317px;height:53px">Phone</div>
  <div class="field" style="left:433px;top:290px;width:317px;height:53px">Email</div>
  <div class="submit">Submit</div>
  <div class="field" style="left:771px;top:155px;width:317px;height:257px">Type your message</div>
</section>

<section class="news">
  <h2>Stay Informed With Our Latest News</h2>
  <div class="email">Enter Your Email</div>
  <div class="subscribe">Subscribe</div>
</section>

<footer class="site-footer">
  <div class="rule" style="top:3241px"></div>
  <div class="brand"><span class="dot"></span>PLATEO.com</div>
  <div class="fcol" style="left:426px">
    <h4>Contact Info</h4>
    <ul>
      <li><svg width="10" height="13" viewBox="0 0 14 18"><path d="M7 0a7 7 0 0 0-7 7c0 5 7 11 7 11s7-6 7-11a7 7 0 0 0-7-7z" fill="#222"/><circle cx="7" cy="7" r="2.5" fill="#fff"/></svg>12b Plateo Lane</li>
      <li><svg width="11" height="11" viewBox="0 0 24 24"><path fill="#222" d="M6.6 10.8a15 15 0 0 0 6.6 6.6l2.2-2.2a1 1 0 0 1 1-.25 11.4 11.4 0 0 0 3.6.57 1 1 0 0 1 1 1V20a1 1 0 0 1-1 1A17 17 0 0 1 3 4a1 1 0 0 1 1-1h3.5a1 1 0 0 1 1 1c0 1.25.2 2.45.57 3.57a1 1 0 0 1-.25 1z"/></svg>+1 555 010 0199</li>
      <li><svg width="13" height="10" viewBox="0 0 16 12"><rect x=".7" y=".7" width="14.6" height="10.6" rx="1" fill="none" stroke="#222" stroke-width="1.4"/><path d="M1 1.5l7 5 7-5" stroke="#222" stroke-width="1.4" fill="none"/></svg>Email: info@plateo.com</li>
    </ul>
  </div>
  <div class="fcol" style="left:661px">
    <h4>Customer Service</h4>
    <ul><li>Terms &amp; conditions</li><li>Privacy Policy</li><li>About Us</li><li>Support</li></ul>
  </div>
  <div class="fcol" style="left:953px">
    <h4>Follow Us</h4>
    <div class="social"><span></span><span></span><span></span><span></span></div>
  </div>
  <div class="rule" style="top:3500px"></div>
  <p class="copyright">©Copyrights 2023 <a>Plateo</a> &nbsp;| &nbsp; All Rights Reserved</p>
</footer>

</body>
</html>
```